Recruitment of Trellan Staffing for the UK market

I want a website for the UK market to attract businesses and companies to come to us for Philipine labour. We want an information site that gives all information on what we do and how we can recruit Philippine labour.
This is a recruitment site for companies to contact us with their requirements for skilled workers coming from the Philipines over to the UK to work.

Target Market(s)

Uk Companies and businesses who want Philipine skilled workers

Industry/Entity Type

REcruitment

Coding

Number of Pages Required

5+ page

Font styles to use
Sans Serif

Colors
0054AA
0677BA
7BADD7
CADEEF
E8F1F8
0094D4
00A9DD
6FCCEA
C7EBF8
E9F6FB
EE7325
F08F49
F5BC92
FAE3D3
FDF4ED
EB3D1F
EC4F4E
F09395
F8D3D4
FCEDEE

Requirements
Must have
• Look professional and corperate with drop down menus for Home ,about, services,articles. training , contact us
Nice to have
• Look at Velmora recruitment- https://velmorarecruitment.example.co.uk/. This is my current site - https://www.trellanstaffing.example.com/
Should not have
• Cartoons or silly pictures , needs to be corperate looking

```html
<!DOCTYPE html>
<html lang="en">
<head>
<meta charset="utf-8">
<title>Trellan Staffing – Skilled Philippine Workers for UK Companies</title>
<link href="https://fonts.googleapis.com/css2?family=Roboto:wght@400;500;700&display=swap" rel="stylesheet">
<style>
:root{
  --red:#EB3D1F;
  --red-soft:#EC4F4E;
  --red-pale:#FCEDEE;
  --ink:#111111;
  --text:#666666;
  --white:#ffffff;
  --line:#eeeeee;
}
*{box-sizing:border-box;margin:0;padding:0}
html,body{width:1200px;height:3857px;overflow:hidden}
body{position:relative;font-family:'Roboto',sans-serif;color:var(--ink);background:var(--white)}
.abs{position:absolute}
.topbar{left:0;top:0;width:1200px;height:4px;background:var(--red-soft)}
.brand{display:flex;align-items:center;gap:10px;font-weight:700;color:var(--red);font-size:30px;letter-spacing:.5px}
.brand .mark{width:22px;height:22px;background:var(--red)}
.site-brand{left:112px;top:38px}
.quote-btn{left:965px;top:22px;width:123px;height:41px;background:var(--red);color:var(--white);border-radius:3px;font-size:15px;font-weight:500;display:flex;align-items:center;justify-content:center}
.main-nav{right:112px;top:78px;display:flex;gap:40px;font-size:15px;font-weight:500}
.hero{left:0;top:123px;width:1200px;height:622px;background:linear-gradient(180deg,#c9c2bb 0%,#9c948d 40%,#6d6661 70%,#585250 100%)}
.hero h1{position:absolute;left:0;width:1200px;top:420px;text-align:center;color:var(--white);font-size:41px;font-weight:500;line-height:52px;text-transform:uppercase}
.btn{background:var(--red);color:var(--white);font-size:15px;font-weight:500;display:flex;align-items:center;justify-content:center;border-radius:3px}
.hero .btn{position:absolute;left:540px;top:538px;width:121px;height:39px}
.workers-title{left:110px;top:848px;width:340px;font-size:30px;font-weight:500;line-height:40px;text-transform:uppercase}
.workers-text{left:111px;top:940px;width:340px;font-size:15px;line-height:29px;color:var(--text)}
.workers-btn{left:111px;top:1134px;width:123px;height:43px}
.skills-grid{left:507px;top:835px;width:573px;height:360px;display:grid;grid-template-columns:repeat(3,1fr);grid-template-rows:repeat(2,1fr);box-shadow:0 2px 14px rgba(0,0,0,.08)}
.skill{display:flex;flex-direction:column;align-items:center;justify-content:flex-end;padding-bottom:30px;font-size:15px;font-weight:500;color:#333;background:var(--white)}
.skill.hot{background:linear-gradient(180deg,var(--red-soft),var(--red));color:var(--white);border-radius:4px}
.skill .icon{width:70px;height:80px;margin-bottom:20px;border-radius:6px;background:#f3d3cf}
.skill.hot .icon{background:rgba(255,255,255,.35)}
.about-title{left:0;width:1200px;top:1312px;text-align:center;font-size:30px;font-weight:500;text-transform:uppercase}
.about-text{left:165px;width:870px;top:1369px;text-align:center;font-size:15px;line-height:26px;color:var(--text)}
.card{top:1488px;width:302px;height:374px;background:var(--white);border-radius:40px;box-shadow:0 4px 14px rgba(0,0,0,.08);text-align:center;padding:40px 36px 0}
.card .badge{width:86px;height:86px;border-radius:50%;background:var(--red);margin:0 auto 16px;display:flex;align-items:center;justify-content:center}
.card h3{font-size:19px;font-weight:500;margin-bottom:14px}
.card p{font-size:12.5px;line-height:22.5px;color:var(--text)}
.card.hot{background:linear-gradient(180deg,var(--red-soft),var(--red));color:var(--white)}
.card.hot p{color:var(--white)}
.card.hot .badge{background:var(--white)}
.band{left:0;top:1987px;width:1200px;height:499px;background:linear-gradient(110deg,#7b4a3a 0%,#4a4340 40%,#3b3a3c 70%,#504a48 100%)}
.band-circle{left:111px;top:2014px;width:444px;height:444px;border-radius:50%;background:var(--white);box-shadow:0 0 0 8px rgba(255,255,255,.6),0 6px 20px rgba(0,0,0,.3);display:flex;align-items:center;justify-content:center;text-align:center;font-size:35px;font-weight:500;line-height:50px;padding:0 70px}
.map{left:123px;top:2578px;width:463px;height:454px;background:linear-gradient(160deg,#8aa7f0,#7c9cf2);border-radius:2px}
.contact-title{left:637px;top:2616px;font-size:30px;font-weight:500;text-transform:uppercase}
.contact-text{left:638px;top:2672px;width:456px;font-size:15px;line-height:27.5px;color:var(--text)}
.contact-list{left:638px;top:2860px;list-style:none;font-size:15px;color:var(--text);line-height:27px}
.contact-list li{display:flex;gap:14px;margin-bottom:10px}
.contact-list svg{flex:none;margin-top:3px}
.footer-brand{left:0;width:1200px;top:3168px;justify-content:center}
.footer-nav{left:0;width:1200px;top:3257px;display:flex;justify-content:center;gap:40px;font-size:15px;font-weight:500}
.socials{left:0;width:1200px;top:3298px;display:flex;justify-content:center;gap:12px}
.socials span{width:24px;height:24px;border-radius:50%;background:var(--red)}
.copyright{left:0;width:1200px;top:3339px;text-align:center;font-size:15px;color:#333}
.team{left:0;top:3370px;width:1200px;height:487px;background:linear-gradient(180deg,#ffffff 0%,#e9e7e5 25%,#8f8f92 60%,#4b4f58 100%)}
</style>
</head>
<body>
<div class="abs topbar"></div>

<header>
  <div class="abs brand site-brand"><span class="mark"></span>Trellan Staffing</div>
  <a class="abs quote-btn">Get A Quote</a>
  <nav class="abs main-nav"><span>Home</span><span>About</span><span>Services</span><span>Articles</span><span>Training</span><span>Contact us</span></nav>
</header>

<section class="abs hero" role="img" aria-label="Photo of job candidates seated in a row of chairs, waiting for interviews">
  <h1>Recruiting and placing skilled Philippine<br>workers into UK companies</h1>
  <a class="btn">Get Started</a>
</section>

<section>
  <h2 class="abs workers-title">UK Skilled Workers List</h2>
  <p class="abs workers-text">The UK government since brexit have developed a new system based on points (similar to Australia) when recruiting from outside of the UK. Previuosly EU citizens could work in the UK without any extensive documentation or clarification of skills. This has all changed.</p>
  <a class="abs btn workers-btn">View All</a>
  <div class="abs skills-grid">
    <div class="skill hot"><div class="icon" role="img" aria-label="Civil engineer icon"></div>Civil engineer</div>
    <div class="skill"><div class="icon" role="img" aria-label="Restaurant manager icon"></div>Restaurant manager</div>
    <div class="skill hot"><div class="icon" role="img" aria-label="Technical director icon"></div>Technical director</div>
    <div class="skill"><div class="icon" role="img" aria-label="Café owner icon"></div>Café owner</div>
    <div class="skill hot"><div class="icon" role="img" aria-label="Electrical engineer icon"></div>Electrical engineer</div>
    <div class="skill"><div class="icon" role="img" aria-label="Internet developer icon"></div>Internet developer</div>
  </div>
</section>

<section>
  <h2 class="abs about-title">What the business is about</h2>
  <p class="abs about-text">We source skilled workers directly from the Philippines to work in the UK. With offices , training locations and specialist recruiters we can find the highest quality individuals to add value and resources to any UK buisness. We delivery quality based on vast experience over a number of years.</p>
  <article class="abs card" style="left:110px">
    <div class="badge" role="img" aria-label="Support agent icon"></div>
    <h3>What we do</h3>
    <p>Our company has been estabilished in the Philippines for over 20 years. We have mainly been recruiting philippine workers for the off shore industry in asia but since brexit and the new rules on skilled workers entering the UK we have been working with UK companies</p>
  </article>
  <article class="abs card hot" style="left:450px">
    <div class="badge" role="img" aria-label="Help chat icon"></div>
    <h3>How we help</h3>
    <p>We work with companies to find skilled workers that meet the UK requirements for Visas and work permits. We guide you through the whole process and deliver highly trained people that add value to your business.</p>
  </article>
  <article class="abs card" style="left:787px">
    <div class="badge"><svg width="46" height="46" viewBox="0 0 46 46" fill="none" stroke="#fff" stroke-width="2.5"><circle cx="23" cy="23" r="19"/><path d="M17 18a6 6 0 1 1 8 5.6c-1.4.6-2 1.6-2 3V28" stroke-linecap="round"/><circle cx="23" cy="33" r="1.2" fill="#fff"/></svg></div>
    <h3>Where to start</h3>
    <p>We need to know what your issues are and how we can understand the personnal you require , over what time frame and the number of employees you need. Once this is estabilished we start sourcing workers in the Philippines that meet your criteria</p>
  </article>
</section>

<section class="abs band" role="img" aria-label="Photo of a hand holding a magnet attracting colourful wooden people figures"></section>
<div class="abs band-circle">We recruit the finest talent available with our dedicated 200 strong team.</div>

<section>
  <div class="abs map" role="img" aria-label="Map of the Philippines"></div>
  <h2 class="abs contact-title">Contact us today</h2>
  <p class="abs contact-text">Please contact us today with your requirements , this can be care workers ,chef, welders, pipe fitters, caravan cabinet makers, medical workers. The UK list of required skills is extensive and the Philippines offersenglish speaking highly qualified hard working employees. Contact us today and make that first step to a highly motivated , quality skilled workforce.</p>
  <ul class="abs contact-list">
    <li><svg width="24" height="24" viewBox="0 0 24 24"><circle cx="12" cy="12" r="12" fill="#EB3D1F"/><path d="M8.5 6.5l2 2-1.2 1.5a7 7 0 0 0 4.7 4.7l1.5-1.2 2 2-1.3 1.8c-5 0-9.5-4.5-9.5-9.5z" fill="#fff"/></svg>07700 900481</li>
    <li><svg width="24" height="24" viewBox="0 0 24 24"><circle cx="12" cy="12" r="12" fill="#EB3D1F"/><rect x="6" y="8" width="12" height="9" rx="1" fill="none" stroke="#fff" stroke-width="1.6"/><path d="M6.5 9l5.5 4 5.5-4" fill="none" stroke="#fff" stroke-width="1.6"/></svg>sales@trellanstaffing.example.com</li>
    <li><svg width="24" height="24" viewBox="0 0 24 24"><circle cx="12" cy="12" r="12" fill="#EB3D1F"/><path d="M12 5a5 5 0 0 1 5 5c0 3.5-5 9-5 9s-5-5.5-5-9a5 5 0 0 1 5-5z" fill="#fff"/><circle cx="12" cy="10" r="2" fill="#EB3D1F"/></svg>Orchard Row, Kelmsby Kelmsby KB4 2<br>United Kingdom</li>
  </ul>
</section>

<footer>
  <div class="abs team" role="img" aria-label="Photo of smiling business professionals seated in a row against a white brick wall"></div>
  <div class="abs brand footer-brand"><span class="mark"></span>Trellan Staffing</div>
  <nav class="abs footer-nav"><span>Home</span><span>About</span><span>Services</span><span>Articles</span><span>Training</span><span>Contact us</span></nav>
  <div class="abs socials" aria-label="Social links"><span></span><span></span><span></span><span></span></div>
  <p class="abs copyright">© 2023 All Rights Reserved | Trellan Staffing Ltd</p>
</footer>
</body>
</html>
```